I need a business card to launch my business. I am a carpenter who works with wood and metal framing. I do commercial and residential properties. I do the final fixtures in expensive residential properties. For example custom made wardrobes, prefinished doors and skirtings. I have an eye for detail and take pride in my work.

I don't want to be pigeon holed as a guy with a tool belt and a hammer. I want to look like a professional company. I want my logo to be modern and young and edgy. I don't have any preference for colours but don't want yellow.

Industry/Entity Type

Residential

Contact Information for Business Card

Oakridge Joinery Co
specialising in residential and commercial fit outs

Mark Delaney
Phone: 0417 358 260
oakridgejoineryco@mailbox-example.net

Logo styles of interest
Pictorial/Combination Logo
Wordmark Logo
Lettermark Logo

```html
<!DOCTYPE html>
<html lang="en">
<head>
<meta charset="utf-8">
<title>Oakridge Joinery Co — Business Card</title>
<link rel="stylesheet" href="https://fonts.googleapis.com/css2?family=Rokkitt:wght@400;600&display=swap">
<style>
  :root {
    --backdrop: #2a2a2a;
    --card: #acacac;
    --bronze: #6a4416;
    --white: #fafafa;
    --card-radius: 26px;
  }
  * { margin: 0; padding: 0; box-sizing: border-box; }
  html, body {
    width: 1200px;
    height: 900px;
    overflow: hidden;
    background: var(--backdrop);
    font-family: "Rokkitt", "Rockwell", serif;
  }
  .canvas {
    position: relative;
    width: 1200px;
    height: 900px;
  }
  .card {
    position: absolute;
    top: 300px;
    width: 510px;
    height: 300px;
    background: var(--card);
    border-radius: var(--card-radius);
  }
  .card--front { left: 60px; }
  .card--back { left: 630px; }

  .wordmark {
    display: flex;
    align-items: center;
    gap: 9px;
    color: var(--bronze);
    font-weight: 600;
    text-transform: uppercase;
    letter-spacing: 1px;
    white-space: nowrap;
  }
  .wordmark__square {
    display: block;
    background: var(--bronze);
  }

  .card--front .wordmark {
    position: absolute;
    top: 100px;
    left: 0;
    right: 0;
    justify-content: center;
    font-size: 26px;
  }
  .card--front .wordmark__square { width: 18px; height: 18px; }

  .tagline {
    position: absolute;
    top: 188px;
    left: 0;
    right: 0;
    text-align: center;
    color: var(--white);
    font-size: 16px;
    line-height: 1.3;
  }
  .accent { color: var(--bronze); }

  .card--back .contact {
    position: absolute;
    right: 26px;
    bottom: 30px;
    text-align: right;
  }
  .card--back .wordmark {
    justify-content: flex-end;
    font-size: 17px;
    margin-bottom: 16px;
  }
  .card--back .wordmark__square { width: 12px; height: 12px; }
  .contact__name {
    color: var(--bronze);
    font-size: 19px;
    font-weight: 600;
    text-transform: uppercase;
    letter-spacing: 0.5px;
    line-height: 1.1;
  }
  .contact__line {
    color: var(--white);
    font-size: 14px;
    line-height: 1.4;
    white-space: nowrap;
  }
</style>
</head>
<body>
  <main class="canvas">
    <section class="card card--front" aria-label="Card front">
      <div class="wordmark">
        <span class="wordmark__square" aria-hidden="true"></span>
        <span class="wordmark__name">Oakridge Joinery Co</span>
      </div>
      <p class="tagline">
        specialising in<br>
        <span class="accent">residential</span> and <span class="accent">commercial</span> fit outs
      </p>
    </section>

    <section class="card card--back" aria-label="Card back">
      <div class="contact">
        <div class="wordmark">
          <span class="wordmark__square" aria-hidden="true"></span>
          <span class="wordmark__name">Oakridge Joinery Co</span>
        </div>
        <p class="contact__name">Mark Delaney</p>
        <p class="contact__line">
          <span class="accent">P:</span> 0417 358 260 //
          <span class="accent">oakridgejoineryco</span>@mailbox-example.net
        </p>
      </div>
    </section>
  </main>
</body>
</html>
```